business card for a massage therapy practice named 'Cedar and Willow Massage Studio'

I really need a trendy, yet easy on the eyes business card to complement my logo. Ideally with some gold or rose gold foil work.

My uploaded file of the logo I have in horizontal but I have a vertical version as well. Another color that is used in the website is a blush pink here and there. I'd like to see some trendy tropical leaves in the design.

```html
<!DOCTYPE html>
<html lang="en">
<head>
<meta charset="utf-8">
<title>Cedar and Willow Massage Studio – Business Card</title>
<link rel="stylesheet" href="https://fonts.googleapis.com/css2?family=Tinos:wght@400&family=Dancing+Script:wght@500&display=swap">
<style>
  :root {
    --backdrop: #ececec;
    --front-pink: #ec8a8f;
    --front-pink-light: #f3a3a6;
    --back-pink: #f6c9c8;
    --back-pink-light: #fbe3e1;
    --gold: #b99a5e;
    --ink: #2a2326;
    --plum: #6e2336;
    --body-text: #3a3336;
  }
  * { margin: 0; padding: 0; box-sizing: border-box; }
  html, body {
    width: 1200px; height: 1200px; overflow: hidden;
    background: var(--backdrop);
  }
  .canvas {
    position: relative; width: 1200px; height: 1200px;
    display: flex; justify-content: center; align-items: center; gap: 100px;
  }
  .card {
    width: 420px; height: 700px;
    border-radius: 4px;
    box-shadow: 0 6px 18px rgba(0,0,0,0.12);
    position: relative;
  }
  .card--front {
    background: linear-gradient(160deg, var(--front-pink-light) 0%, var(--front-pink) 55%, var(--front-pink-light) 100%);
    display: flex; align-items: center; justify-content: center;
  }
  .card--back {
    background: linear-gradient(160deg, var(--back-pink) 0%, var(--back-pink-light) 50%, var(--back-pink) 100%);
    text-align: center;
    font-family: "Tinos", "Times New Roman", serif;
    color: var(--body-text);
  }
  .brand {
    display: flex; align-items: center; gap: 12px;
    font-family: "Tinos", "Times New Roman", serif;
    color: var(--ink);
    font-size: 22px; line-height: 1.15;
  }
  .brand__dot {
    width: 34px; height: 34px; border-radius: 50%;
    background: var(--gold); flex: none;
  }
  .card--back .brand {
    position: absolute; top: 60px; left: 40px;
    text-align: left; font-size: 21px;
  }
  .person { position: absolute; top: 180px; width: 100%; }
  .person__name {
    font-family: "Dancing Script", cursive;
    font-size: 44px; color: var(--plum); font-weight: 500;
  }
  .person__role { font-size: 17px; margin-top: 2px; }
  .address {
    position: absolute; top: 330px; width: 100%;
    font-size: 18px; line-height: 1.6;
  }
  .contact {
    position: absolute; top: 450px; width: 100%;
    font-size: 19px; line-height: 2.05;
  }
</style>
</head>
<body>
<main class="canvas">
  <section class="card card--front" aria-label="Card front">
    <div class="brand">
      <span class="brand__dot"></span>
      <span>Cedar and Willow<br>Massage Studio</span>
    </div>
  </section>

  <section class="card card--back" aria-label="Card back">
    <div class="brand">
      <span class="brand__dot"></span>
      <span>Cedar and Willow<br>Massage Studio</span>
    </div>
    <div class="person">
      <p class="person__name">John Doe</p>
      <p class="person__role">Director</p>
    </div>
    <div class="address">
      <p>Dummy city</p>
      <p>Dummy Country Land</p>
    </div>
    <div class="contact">
      <p>1-234-567890</p>
      <p>john@cedarandwillow.com</p>
      <p>www.cedarandwillow.com</p>
    </div>
  </section>
</main>
</body>
</html>
```